Unique Private Wine Label for Wine Bottles (UPDATED BRIEF)

Updated Brief Oct 15, 2017. Please see below!

I am looking for a unique wine label designs for my wine bottles. I create wine and would like to have wine labels for my bottles. I am looking for a main label and then several additional labels with the same design just with the type of wine listed on the label (see below for wine types). This is private wine for family and friends to consume not commercially produced wine.

I would like a rustic, classic or vintage design with some color in the label. I do have a specific name for the wine which i like to call "Thornfield" . I would like to see different designs.

We would like vintage or classic labels. Please give me a few multiple designs based on above. I also want to have a main label and then incorporate different types of wine into the labels like "Chardonnay" or "Pinot Noir" or "Sauvignon Blanc" or "Caberent Savignon" or "Merlot" below the name of the wine. As an example, the labels will be the same design but the word Sauvignon Blanc will be incorporated into the design for this type of wine label and so on for the other types of wine.

Please let me know if you have any questions.
Updates

Project Deadline Extended
Reason: I Have changed the vision of the design. I would like a classic, rustic or vintage design NOT a beach theme. The brief has been updated as of Oct 15, 2017. Please see updated brief for instructions on new design

Note: I have changed the vision of the design. I would like a classic, rustic or vintage design NOT a beach theme. The brief has been updated as of Oct 15, 2017. Please see updated brief for instructions on new design. I would like new designers to provide new designs! Payment is Guaranteed! Thanks!

Target Market(s)

This is private wine for family and friends to consume not commercially produced wine.

Font styles to use
Decorative
Script

Colors

Designer to choose colors to be used in the design.

Requirements
Must have
• Updated Brief Oct 15, 2017. Please see below!
• I am looking for a unique wine label designs for my wine bottles. I create wine and would like to have wine labels for my bottles. I am looking for a main label and then several additional labels with the same design just with the type of wine listed on the label (see below for wine types). This is private wine for family and friends to consume not commercially produced wine.
• I would like a rustic, classic or vintage design with some color in the label. I do have a specific name for the wine which i like to call "Thornfield". I would like to see different designs.
• We would like vintage or classic labels. Please give me a few multiple designs based on above. I also want to have a main label and then incorporate different types of wine into the labels like "Chardonnay" or "Pinot Noir" or "Sauvignon Blanc" or "Caberent Savignon" or "Merlot" below the name of the wine. As an example, the labels will be the same design but the word Sauvignon Blanc will be incorporated into the design for this type of wine label and so on for the other types of wine.
• Please let me know if you have any questions.
Nice to have
Should not have
• Please see the updated brief instructions above. I DO NOT WANT A BEACH THEME ANYMORE!

```html
<!DOCTYPE html>
<html lang="en">
<head>
<meta charset="utf-8">
<title>Thornfield Vineyards – Wine Label</title>
<link rel="stylesheet" href="https://fonts.googleapis.com/css2?family=Playfair+Display:wght@700;900&family=Libre+Baskerville:ital@0;1&display=swap">
<style>
  :root {
    --backdrop: #7d0101;
    --label-black: #060504;
    --gold: #c9a04a;
    --gold-light: #e8cf8a;
    --gold-dark: #8f6a22;
  }
  * { margin: 0; padding: 0; box-sizing: border-box; }
  html, body {
    width: 846px;
    height: 1200px;
    overflow: hidden;
    background: var(--backdrop);
  }
  .canvas {
    position: relative;
    width: 846px;
    height: 1200px;
  }
  .wine-label {
    position: absolute;
    left: 123px;
    top: 220px;
    width: 600px;
    height: 760px;
    background: var(--label-black);
    color: var(--gold);
  }
  .label-frame {
    position: absolute;
    inset: 0;
  }
  .crest-ornament {
    position: absolute;
    left: 190px;
    top: 58px;
    width: 220px;
    height: 110px;
    border-radius: 8px;
    background: linear-gradient(180deg, var(--gold-light), var(--gold-dark));
    opacity: 0.85;
  }
  .wine-name {
    position: absolute;
    left: 0;
    right: 0;
    top: 190px;
    text-align: center;
    font-family: "Playfair Display", Georgia, serif;
    font-weight: 900;
    font-size: 62px;
    line-height: 1.02;
    letter-spacing: 1px;
    text-transform: uppercase;
    background: linear-gradient(180deg, var(--gold-light) 0%, var(--gold) 50%, var(--gold-dark) 100%);
    -webkit-background-clip: text;
    background-clip: text;
    color: transparent;
  }
  .vine-illustration {
    position: absolute;
    left: 150px;
    top: 350px;
    width: 300px;
    height: 230px;
    border-radius: 12px;
    background: radial-gradient(ellipse at 55% 55%, var(--gold-light), var(--gold-dark) 80%);
    opacity: 0.9;
  }
  .label-note {
    position: absolute;
    left: 120px;
    right: 120px;
    top: 605px;
    text-align: center;
    font-family: "Libre Baskerville", Georgia, serif;
    font-style: italic;
    font-size: 12px;
    line-height: 1.55;
    color: var(--gold-light);
  }
  .vintage-year,
  .bottle-volume {
    position: absolute;
    bottom: 42px;
    font-family: "Libre Baskerville", Georgia, serif;
    font-size: 16px;
    color: var(--gold-light);
    letter-spacing: 0.5px;
  }
  .vintage-year { left: 52px; }
  .bottle-volume { right: 52px; }
</style>
</head>
<body>
<main class="canvas">
  <section class="wine-label">
    <svg class="label-frame" width="600" height="760" viewBox="0 0 600 760" aria-hidden="true">
      <path d="M50,20 H550 A30,30 0 0 0 580,50 V710 A30,30 0 0 0 550,740 H50 A30,30 0 0 0 20,710 V50 A30,30 0 0 0 50,20 Z"
            fill="none" stroke="var(--gold)" stroke-width="3"/>
      <path d="M58,30 H542 A28,28 0 0 0 570,58 V702 A28,28 0 0 0 542,730 H58 A28,28 0 0 0 30,702 V58 A28,28 0 0 0 58,30 Z"
            fill="none" stroke="var(--gold-dark)" stroke-width="1"/>
    </svg>

    <div class="crest-ornament" role="img" aria-label="Gold scrollwork crest with a row of five stars"></div>

    <h1 class="wine-name">Thornfield<br>Vineyards</h1>

    <div class="vine-illustration" role="img" aria-label="Gold grape bunch with vine leaves beside a small wine bottle and glass"></div>

    <p class="label-note">Hand crafted in small batches from our family vines, aged with patience and shared with the people we love most around the table.</p>

    <span class="vintage-year">2017</span>
    <span class="bottle-volume">750ML</span>
  </section>
</main>
</body>
</html>
```